Design the Business card for NetVaultic

Business card required for a professional Cyber Security business.
Company Logo and Icon has already been provided however I would like other options for the logo and icon to compare to. Alternatively, please refine/enhance the image of the logo.icon I have already provided.

If you are going to use the provided logo and icon, I was thinking that the company raised Logo on White background would serve well on the front of the card. See attached. AND, a large company raised stand-alone icon to appear on black background on the back of the card with tagline 'Cyber Risk Management, Governance and Consulting' or 'Cyber Security for your Business' See attached.
Alternatively, provide your own design for the logo and icon.

Target Market(s)

Enterprise, Government, Financial.

Contact Information for Business Card

Tavin Orloweth
Founder and CEO

Email Address
Mobile Number
Website URL
LinkedIn URL

Logo Text

NetVaultic - see attached example of logo

Font styles to use
Other font styles liked:
• Berlin Sans FB

Requirements
Must have
• Clean large and bold icon on the back with tagline.
• Horizontal alignment,
Nice to have
• Round edges.
• Raised Logo/Icon
Should not have
• An unprofessional look and feel.

```html
<!DOCTYPE html>
<html lang="en">
<head>
<meta charset="utf-8">
<title>NetVaultic Business Card</title>
<link href="https://fonts.googleapis.com/css2?family=Cabin:wght@500;600&family=Roboto+Condensed:wght@700&family=Roboto:wght@400;500&display=swap" rel="stylesheet">
<style>
  :root {
    --backdrop: #1f1f20;
    --brand-blue: #0a6fc2;
    --accent-yellow: #ffc20e;
    --dot-blue: #3f6fc8;
    --paper: #efefef;
    --card-black: #1b1c1e;
    --card-edge: #2a2b2e;
    --tag-blue: #4f73c9;
    --white: #ffffff;
  }
  * { margin: 0; padding: 0; box-sizing: border-box; }
  html, body { width: 1200px; height: 960px; overflow: hidden; }
  body { background: var(--backdrop); position: relative; font-family: "Roboto", Arial, sans-serif; }

  .card {
    position: absolute;
    width: 600px;
    height: 342px;
    border-radius: 18px;
    overflow: hidden;
  }
  .card-front { left: 322px; top: 108px; background: var(--paper); }
  .card-back { left: 321px; top: 494px; background: var(--card-black); border: 1px solid var(--card-edge); }

  .front-shape { position: absolute; inset: 0; }

  .contact-block { position: absolute; left: 28px; top: 100px; color: var(--white); }
  .person-name {
    font-family: "Roboto Condensed", Arial, sans-serif;
    font-weight: 700; font-size: 22px; color: var(--accent-yellow);
    letter-spacing: 0.2px; line-height: 26px;
  }
  .person-title { font-weight: 500; font-size: 14px; line-height: 20px; margin-bottom: 14px; }
  .contact-list { list-style: none; }
  .contact-item { display: flex; align-items: center; gap: 9px; font-size: 14px; line-height: 19px; }
  .contact-icon { width: 14px; height: 14px; flex: none; }

  .front-brand {
    position: absolute; left: 300px; top: 145px;
    display: flex; align-items: center; gap: 12px;
  }
  .brand-dot { width: 46px; height: 46px; border-radius: 50%; background: var(--brand-blue); }
  .brand-name {
    font-family: "Cabin", Arial, sans-serif; font-weight: 600;
    font-size: 36px; color: var(--brand-blue);
  }

  .back-brand {
    position: absolute; left: 0; right: 0; top: 62px;
    display: flex; flex-direction: column; align-items: center; gap: 16px;
  }
  .back-dot { width: 118px; height: 118px; border-radius: 50%; background: var(--tag-blue); }
  .back-name { font-family: "Cabin", Arial, sans-serif; font-weight: 600; font-size: 30px; color: var(--tag-blue); }

  .tagline {
    position: absolute; left: 0; right: 0; top: 274px; text-align: center;
    font-family: "Cabin", Arial, sans-serif; font-weight: 500; font-size: 19px;
  }
  .tagline-blue { color: var(--tag-blue); }
  .tagline-yellow { color: var(--accent-yellow); }
</style>
</head>
<body>

<section class="card card-front">
  <svg class="front-shape" width="600" height="342" viewBox="0 0 600 342">
    <path d="M0 0 H300 Q183 171 305 342 H0 Z" fill="var(--brand-blue)"/>
    <path d="M300 0 Q183 171 305 342" fill="none" stroke="var(--accent-yellow)" stroke-width="4"/>
    <circle cx="298" cy="12" r="8" fill="var(--dot-blue)" stroke="var(--white)" stroke-width="2"/>
    <circle cx="296" cy="330" r="8" fill="var(--dot-blue)" stroke="var(--white)" stroke-width="2"/>
  </svg>

  <div class="contact-block">
    <h1 class="person-name">TAVIN ORLOWETH</h1>
    <p class="person-title">FOUNDER &amp; CEO</p>
    <ul class="contact-list">
      <li class="contact-item">
        <svg class="contact-icon" viewBox="0 0 14 14"><rect x="3.5" y="0.5" width="7" height="13" rx="1.5" fill="none" stroke="var(--accent-yellow)" stroke-width="1.6"/><circle cx="7" cy="11" r="0.9" fill="var(--accent-yellow)"/></svg>
        <span>555 014 2738</span>
      </li>
      <li class="contact-item">
        <svg class="contact-icon" viewBox="0 0 14 14"><rect x="1" y="3" width="12" height="8.5" fill="var(--accent-yellow)"/><path d="M1 3 L7 8 L13 3" fill="none" stroke="var(--brand-blue)" stroke-width="1.2"/></svg>
        <span>tavin@netvaultic.com</span>
      </li>
      <li class="contact-item">
        <svg class="contact-icon" viewBox="0 0 14 14"><circle cx="7" cy="7" r="6.3" fill="var(--accent-yellow)"/><path d="M1 7 H13 M7 1 Q3.5 7 7 13 M7 1 Q10.5 7 7 13" fill="none" stroke="var(--brand-blue)" stroke-width="1"/></svg>
        <span>www.netvaultic.com</span>
      </li>
      <li class="contact-item">
        <svg class="contact-icon" viewBox="0 0 14 14"><circle cx="7" cy="7" r="6.3" fill="var(--accent-yellow)"/></svg>
        <span>netvaultic</span>
      </li>
    </ul>
  </div>

  <div class="front-brand">
    <span class="brand-dot"></span>
    <span class="brand-name">NetVaultic</span>
  </div>
</section>

<section class="card card-back">
  <div class="back-brand">
    <span class="back-dot"></span>
    <span class="back-name">NetVaultic</span>
  </div>
  <p class="tagline"><span class="tagline-blue">Cyber Risk Management,</span> <span class="tagline-yellow">Governance &amp; Consulting</span></p>
</section>

</body>
</html>
```